Looking to Redesign Brevonix.com website

You guys did one of the brochures for brevonix.com and I would like to see if we can go ahead and get an estimate for a redesigned web site for the company. We currently have a couple of pages on brevonix.com which are very much a starter type site.

The new design will need to reflect some of the things discussed in the brochure. It will have flash. Needs to be designed for simple hosting using cpanels.

The site needs to have between 12 and 15 pages with flash pages to move through features. Integrated with twitter like it is now, and contact forms delivered from our CRM along with other interactive features such as subscription to newsletter, etc...

I don't have lots of details on how to proceed yet, but here are some competitor sites:

Can we take a look at potential costs involved in the redo of the site as vague as my description above can permit.

Target Market(s)

Business to Business

Number of Pages Required

5+ page

Font styles to use
Sans Serif

Requirements
Must have
• Must have professional feel. Similar to brochure. and logo.
• Include our story in the discussion.
• embedded links to our CRM for popup contact forms.
• Logo files and 2 types of brochures uploaded.
• Important to keep color scheme
Nice to have
• Flash and some movement
Should not have
• Not sure yet

```html
<!DOCTYPE html>
<html lang="en">
<head>
<meta charset="utf-8">
<title>Brevonix – Hosted PBX Services</title>
<link rel="stylesheet" href="https://fonts.googleapis.com/css2?family=Roboto:wght@400;700;900&family=Open+Sans:ital,wght@0,400;0,600;1,400&display=swap">
<style>
:root{
  --red:#c80a0a;
  --red-dark:#a30000;
  --ink:#222;
  --muted:#555;
  --black:#111;
  --footer:#3b3b3f;
  --footer-text:#c9c9c9;
  --white:#fff;
  --blue-1:#1f4f7a;
  --blue-2:#7aa3c4;
}
*{box-sizing:border-box;margin:0;padding:0}
html,body{width:1200px;height:3830px;overflow:hidden;background:var(--white)}
body{font-family:"Open Sans",Arial,sans-serif;color:var(--ink);position:relative}
.head{font-family:"Roboto",Arial,sans-serif;font-weight:700;text-transform:uppercase}
section,header,footer{position:absolute;left:0;width:1200px}
.btn{display:inline-block;background:var(--red);color:var(--white);font-family:"Roboto",sans-serif;font-weight:700;font-size:14px;text-transform:uppercase;padding:14px 32px;border-radius:3px}

/* header */
.topbar{top:0;height:90px;background:var(--black);display:flex;align-items:center}
.brand{position:absolute;left:100px;top:18px;display:flex;align-items:center;gap:10px;color:var(--white);font-family:"Roboto",sans-serif;font-weight:700;font-size:20px}
.brand-dot{width:52px;height:52px;border-radius:50%;background:var(--red)}
.nav{position:absolute;left:302px;top:38px;display:flex;gap:42px;color:var(--white);font-family:"Roboto",sans-serif;font-weight:700;font-size:13px;text-transform:uppercase}

/* hero */
.hero{top:90px;height:540px}
.hero-photo{position:absolute;inset:0;background:radial-gradient(ellipse at 50% 35%,#9a9a9a 0%,#5a5a5a 55%,#2c2c2c 100%)}
.hero-title{position:absolute;top:218px;width:100%;text-align:center;color:var(--white);font-size:38px;letter-spacing:1px}
.hero .btn{position:absolute;top:282px;left:510px}
.hero-curve{position:absolute;bottom:0;left:0}

/* welcome */
.welcome{top:720px;text-align:center}
.welcome h1{color:var(--red);font-size:25px;line-height:34px}
.welcome h1 span{color:var(--black)}
.welcome p{width:780px;margin:26px auto 0;font-size:14px;line-height:29px;color:var(--muted)}

/* benefits */
.benefits{top:1000px;text-align:center}
.benefits h2{color:var(--red);font-size:25px}
.benefits .lead{margin-top:20px;font-size:14px;color:var(--muted)}
.benefit-row{position:absolute;top:112px;left:120px;width:960px;display:flex;justify-content:space-between}
.benefit{width:240px;text-align:center}
.benefit-icon{width:108px;height:108px;border-radius:50%;background:var(--red);margin:0 auto;display:flex;align-items:center;justify-content:center}
.benefit h3{margin-top:22px;font-size:15px;color:var(--red)}
.benefit p{font-size:13px;color:var(--muted);margin-top:8px;line-height:20px}
.slider-arrow{position:absolute;top:150px;color:#aaa;font-size:26px}

/* features */
.features{top:1381px;height:620px}
.features-photo{position:absolute;left:0;top:0;width:600px;height:620px;background:linear-gradient(135deg,#f4ece6 0%,#d9c9bd 55%,#8e7b6f 100%)}
.features-panel{position:absolute;left:600px;top:0;width:600px;height:620px;background:var(--red);color:var(--white);padding:58px 0 0 82px}
.features-panel h2{font-size:24px;margin-bottom:24px}
.feature-list{list-style:none;font-size:12.5px;line-height:18px;font-weight:600}
.feature-list li{position:relative;padding-left:22px;margin-bottom:13px;width:460px}
.feature-list li::before{content:"";position:absolute;left:2px;top:4px;width:8px;height:4px;border-left:2px solid var(--white);border-bottom:2px solid var(--white);transform:rotate(-45deg)}

/* why */
.why{top:2068px;height:440px}
.monitor{position:absolute;left:100px;top:25px}
.why-text{position:absolute;left:672px;top:60px;width:400px}
.why-text h2{font-size:24px;color:var(--red);margin-bottom:16px}
.why-text p{font-size:14px;line-height:26px;color:var(--muted)}
.why-text .btn{margin-top:24px}

/* about */
.about{top:2545px;height:510px}
.about-photo{position:absolute;inset:0;background:linear-gradient(90deg,var(--blue-1) 0%,#2f6794 45%,var(--blue-2) 100%)}
.about-curve{position:absolute;top:0;left:0}
.about-text{position:absolute;left:100px;top:130px;width:620px;color:var(--white)}
.about-text h2{font-size:27px;margin-bottom:18px}
.about-text p{font-size:14px;line-height:26px;margin-bottom:26px}

/* testimonials */
.clients{top:3130px;height:320px}
.clients h2{text-align:center;color:var(--red);font-size:23px}
.client-photo{position:absolute;left:158px;top:80px;width:190px;height:190px;border-radius:50%;background:radial-gradient(circle at 50% 45%,#d9d9d9,#8f8f8f)}
.quote{position:absolute;left:420px;top:110px;width:600px;font-style:italic;font-size:13px;line-height:22px;color:var(--muted)}
.quote-mark{position:absolute;font-family:Georgia,serif;font-size:46px;color:#bbb}
.client-name{position:absolute;left:440px;top:218px;font-family:"Roboto",sans-serif;font-weight:700;color:var(--red);font-size:15px}
.client-role{position:absolute;left:440px;top:242px;font-size:12px;color:var(--muted)}

/* footer */
.footer{top:3472px;height:358px;background:var(--footer);color:var(--footer-text);font-size:12px}
.foot-brand{position:absolute;left:100px;top:18px;display:flex;align-items:center;gap:8px;font-family:"Roboto",sans-serif;font-weight:700;color:var(--white);font-size:16px}
.foot-brand i{width:40px;height:40px;border-radius:50%;background:#777;display:block}
.foot-policy{position:absolute;left:100px;top:110px;width:240px}
.foot-policy h3{color:var(--white);font-size:17px;margin-bottom:10px}
.foot-policy p{line-height:19px}
.foot-links{position:absolute;top:110px;list-style:none;line-height:26px}
.social{position:absolute;left:758px;top:48px;display:flex;gap:10px}
.social i{width:28px;height:28px;border-radius:50%;background:#cfcfcf;display:block}
.newsletter{position:absolute;left:762px;top:106px}
.newsletter h3{color:var(--white);font-size:17px;margin-bottom:14px}
.nl-form{display:flex}
.nl-input{width:238px;height:38px;background:#2c2c30;color:#999;padding:11px 14px;font-size:12px}
.nl-btn{width:96px;height:38px;background:var(--red);color:var(--white);font-family:"Roboto",sans-serif;font-weight:700;font-size:13px;text-align:center;line-height:38px;margin-left:8px}
.contact-line{margin-top:16px;display:flex;align-items:center;gap:10px}
.contact-line::before{content:"";width:9px;height:9px;background:var(--red);display:block}
.copyright{position:absolute;bottom:22px;width:100%;text-align:center;font-size:11px;color:#999}
</style>
</head>
<body>

<header class="topbar">
  <div class="brand"><span class="brand-dot"></span>Brevonix</div>
  <nav class="nav"><span>About</span><span>Why Brevonix</span><span>Features</span><span>Advantages</span><span>Best of Class Hardware</span><span>Support</span><span>Contact</span></nav>
</header>

<section class="hero">
  <div class="hero-photo" role="img" aria-label="Business people standing on a world map backdrop"></div>
  <h1 class="hero-title head">Brevonix Invenient Veritatem</h1>
  <span class="btn">Contact Here!</span>
  <svg class="hero-curve" width="1200" height="90" viewBox="0 0 1200 90">
    <path d="M0 30 Q600 110 1200 0 L1200 90 L0 90 Z" fill="var(--red)"/>
    <path d="M0 55 Q600 125 1200 30 L1200 90 L0 90 Z" fill="#fff"/>
  </svg>
</section>

<section class="welcome">
  <h1 class="head"><span>Welcome to</span><br>Brevonix Invenient Veritatem</h1>
  <p>Brevonix has been in the business of providing Hosted based PBX services since early 2003. This is before most of the business world had ever heard of such a service.</p>
  <p style="margin-top:16px">Yes. You may have never heard of us or our services… Fact is we have been providing services to corporate clients as a part of an IT managed services group and were not marketing to other businesses.</p>
</section>

<section class="benefits">
  <h2 class="head">Benefits</h2>
  <p class="lead">Discovering your needs, creating solutions that truly work</p>
  <span class="slider-arrow" style="left:76px">‹</span>
  <span class="slider-arrow" style="right:76px">›</span>
  <div class="benefit-row">
    <div class="benefit">
      <div class="benefit-icon"><svg width="50" height="50" viewBox="0 0 50 50"><path d="M38 8 C26 10 18 20 14 30 L20 36 C30 32 40 24 42 12 Z" fill="#fff"/><path d="M14 30 L8 44 L20 36 Z" fill="#fff"/></svg></div>
      <h3 class="head">Quick ROI</h3><p>Equipment is included in the service<br>Secure: Encrypted lines</p>
    </div>
    <div class="benefit">
      <div class="benefit-icon"><svg width="50" height="50" viewBox="0 0 50 50"><circle cx="25" cy="25" r="14" fill="none" stroke="#fff" stroke-width="7" stroke-dasharray="6 4"/><circle cx="25" cy="25" r="5" fill="#fff"/></svg></div>
      <h3 class="head">Easy Installation</h3><p>Very little business interruption</p>
    </div>
    <div class="benefit">
      <div class="benefit-icon"><svg width="50" height="50" viewBox="0 0 50 50"><rect x="8" y="18" width="24" height="24" fill="none" stroke="#fff" stroke-width="4"/><path d="M22 28 L40 10 M30 10 H40 V20" fill="none" stroke="#fff" stroke-width="4"/></svg></div>
      <h3 class="head">Expandable</h3><p>One unit at a time</p>
    </div>
    <div class="benefit">
      <div class="benefit-icon"><svg width="50" height="50" viewBox="0 0 50 50"><path d="M20 10 V30 L14 26 L12 30 L22 42 H36 L38 26 L26 22 V10 Z" fill="#fff"/></svg></div>
      <h3 class="head">Intuitive</h3><p>Easy to learn and run</p>
    </div>
  </div>
</section>

<section class="features">
  <div class="features-photo" role="img" aria-label="Smiling support agent wearing a headset"></div>
  <div class="features-panel">
    <h2 class="head">Features</h2>
    <ul class="feature-list">
      <li>Integrated phone services for one desk to 100 and beyond</li>
      <li>Work wherever you or your employees are – from home, the office, the beach! Brevonix follows you</li>
      <li>Flexible system designed for the unique needs of your company</li>
      <li>Connect multiple locations into one system</li>
      <li>No huge investments, Brevonix provides the system, just “plug and play”</li>
      <li>Easy to add one station at a time as your business grows</li>
      <li>Expand employee options by setting up work at home stations</li>
      <li>Tech support that responds promptly, and personally</li>
      <li>Secure, encrypted technology</li>
      <li>Automated call routing based on location of incoming calls. (Not only based on location but a wide variety of rules that are chosen by the client)</li>
      <li>Programmable speed dialing</li>
    </ul>
  </div>
</section>

<section class="why">
  <svg class="monitor" width="490" height="395" viewBox="0 0 490 395">
    <rect x="0" y="0" width="490" height="300" rx="8" fill="#1a1a1a"/>
    <rect x="14" y="14" width="462" height="272" fill="#f3f3ee" role="img" aria-label="Unified communication network diagram"/>
    <path d="M200 300 L290 300 L300 370 L190 370 Z" fill="#c9c9c9"/>
    <ellipse cx="245" cy="378" rx="95" ry="10" fill="#d9d9d9"/>
  </svg>
  <div class="why-text">
    <h2 class="head">Why Brevonix</h2>
    <p>Honestly, your office phone system is probably the least sexy thing in your company – the minute the system is down, you're out of business – so you need a phone system that you can count on every minute of every day. But your phone system doesn't have to be boring, it can look great, too! With a sleek design and customized logos, these phones add a distinctive look sitting on the desk. What is even better, is how good this system makes you look to your customers…</p>
    <span class="btn">Read More Info</span>
  </div>
</section>

<section class="about">
  <div class="about-photo" role="img" aria-label="Businessman touching a network of people icons"></div>
  <svg class="about-curve" width="1200" height="80" viewBox="0 0 1200 80"><path d="M0 0 H1200 V20 Q600 100 0 50 Z" fill="#fff"/></svg>
  <svg style="position:absolute;left:0;bottom:0" width="1200" height="70" viewBox="0 0 1200 70"><path d="M0 70 H1200 V0 Q700 80 0 40 Z" fill="#fff"/></svg>
  <div class="about-text">
    <h2 class="head">About Brevonix</h2>
    <p>Brevonix has been in the business of providing Hosted based PBX services since early 2003. This is before most of the business world had ever heard of such a service.</p>
    <p>Yes. You may have never heard of us or our services… Fact is we have been providing services to corporate clients as a part of an IT managed services group and were not marketing to other businesses.</p>
    <span class="btn">Read More Info</span>
  </div>
</section>

<section class="clients">
  <h2 class="head">What Our Client's Say</h2>
  <div class="client-photo" role="img" aria-label="Client portrait"></div>
  <span class="quote-mark" style="left:412px;top:78px">“</span>
  <p class="quote">Lorem Ipsum is simply dummy text of the printing and typesetting industry. Lorem Ipsum has been the industry's standard dummy text ever since the 1500s, when an unknown printer took a galley of type and scrambled it to make a type specimen book…</p>
  <span class="quote-mark" style="left:1020px;top:178px">”</span>
  <span class="client-name">Marcus Hale</span>
  <span class="client-role">Business man</span>
</section>

<footer class="footer">
  <div class="foot-brand"><i></i>Brevonix</div>
  <div class="foot-policy">
    <h3 class="head">Privay Policy</h3>
    <p>Lorem Ipsum is simply dummy text of the printing and typesetting industry. Lorem Ipsum has been the industry's standard dummy text ever since the 1500s</p>
  </div>
  <ul class="foot-links" style="left:405px"><li>Home</li><li>About Why Brevonix</li><li>Features</li><li>Advantages</li><li>Best of Class Hardware</li><li>Support</li></ul>
  <ul class="foot-links" style="left:598px"><li>Terms &amp; Conditions</li><li>Privacy policy</li><li>Disclaimer</li><li>Sitemap</li></ul>
  <div class="social"><i></i><i></i><i></i><i></i></div>
  <div class="newsletter">
    <h3 class="head">Newsletter Subscribe</h3>
    <div class="nl-form"><span class="nl-input">Enter your email id</span><span class="nl-btn">SIGNUP</span></div>
    <div class="contact-line" style="margin-top:22px">Phone : +1 555 014 2290</div>
    <div class="contact-line">Email : sales@brevonix.com</div>
  </div>
  <div class="copyright">Copyright © 2016, Brevonix. All rights reserved.</div>
</footer>

</body>
</html>
```